Modern Attractive Letterhead for Veterinary House Call Business.

A letterhead which can be printed on A4, A5 and A6 paper sizes.
To have: ( our files to be uploaded)
1. Logo with Text
2. telephone
3. email
4. website
5. Address

Target Market(s)

60-85year mainly women pet owners. Also market include families, young professionals, busy people who have dogs and cats

Industry/Entity Type

Business

Requirements
Must have
• 1. Logo with Text ( provided)
• 2. telephone
• 3. email
• 4. website
• 5. Address
Nice to have
• Needs to be modern, preferably warm and caring in nature( if possible )
Should not have
• difficulty in printing A5 and A6

```html
<!DOCTYPE html>
<html lang="en">
<head>
<meta charset="utf-8">
<title>Hearthside Vet Care – Letterhead</title>
<link rel="stylesheet" href="https://fonts.googleapis.com/css2?family=Cinzel:wght@400;600&display=swap">
<style>
  :root {
    --backdrop: #ecebe8;
    --paper: #ffffff;
    --band-deep: #0f3aa6;
    --band-mid: #2f86d8;
    --band-light: #4fd6fb;
    --accent-green: #6cc11d;
    --brand-blue: #1d4fb8;
    --ink: #1a1a1a;
    --rule: #9a9a9a;
    --ghost: #e6ebf6;
  }
  * { box-sizing: border-box; margin: 0; padding: 0; }
  html, body {
    width: 1017px; height: 1200px; overflow: hidden;
    background: var(--backdrop);
  }
  .letterhead {
    position: absolute; left: 33px; top: 27px;
    width: 820px; height: 1061px;
    background: var(--paper);
    box-shadow: 0 2px 8px rgba(0,0,0,0.18);
    overflow: hidden;
    font-family: "Cinzel", "Times New Roman", serif;
    color: var(--ink);
  }
  .side-band {
    position: absolute; left: 0; top: 0; width: 42px; height: 100%;
    background: linear-gradient(to bottom,
      var(--band-deep) 0%, var(--band-mid) 22%, var(--band-light) 38%,
      var(--band-mid) 50%, var(--band-light) 64%, var(--band-mid) 80%, var(--band-deep) 100%);
  }
  .side-rule {
    position: absolute; left: 46px; top: 0; width: 2px; height: 100%;
    background: var(--accent-green);
  }
  .brand {
    position: absolute; left: 16px; top: 34px;
    display: flex; align-items: center; gap: 14px;
  }
  .brand-disc {
    width: 90px; height: 90px; border-radius: 50%;
    background: var(--paper);
    display: flex; align-items: center; justify-content: center;
  }
  .brand-disc span {
    width: 58px; height: 58px; border-radius: 50%;
    background: var(--brand-blue);
  }
  .brand-name {
    font-weight: 600; font-size: 31px; letter-spacing: 0.5px;
    color: var(--brand-blue); line-height: 1;
  }
  .contact {
    position: absolute; left: 523px; top: 38px;
    border-left: 1px solid var(--rule);
    padding-left: 8px;
    list-style: none;
  }
  .contact li {
    display: flex; align-items: center; gap: 8px;
    font-size: 15px; height: 27px;
  }
  .contact svg { width: 17px; height: 17px; flex: none; }
  .address {
    position: absolute; left: 54px; bottom: 21px;
    display: flex; align-items: center; gap: 6px;
    font-size: 17px;
  }
  .address svg { width: 18px; height: 18px; }
  .pet-watermark {
    position: absolute; left: 585px; top: 715px;
    width: 240px; height: 350px;
    border-radius: 48% 52% 0 0 / 40% 40% 0 0;
    background: radial-gradient(ellipse at 50% 40%, var(--ghost) 0%, rgba(230,235,246,0.55) 60%, rgba(255,255,255,0) 100%);
  }
</style>
</head>
<body>
  <main class="letterhead">
    <div class="side-band"></div>
    <div class="side-rule"></div>

    <header class="brand">
      <div class="brand-disc"><span></span></div>
      <div class="brand-name">Hearthside Vet Care</div>
    </header>

    <ul class="contact">
      <li>
        <svg viewBox="0 0 20 20"><circle cx="10" cy="10" r="8.5" fill="none" stroke="#2f86d8" stroke-width="1.6"/><path d="M7 5.5c-1 2.5 0.5 7 5 9l1.5-1.8-2-1.4-1 .8c-1.3-.8-2.2-2-2.6-3.3l1-.7-.8-2.4z" fill="#1d4fb8"/></svg>
        0400 123 456
      </li>
      <li>
        <svg viewBox="0 0 20 20"><rect x="2" y="5" width="16" height="11" fill="#1d4fb8"/><path d="M2 5l8 6 8-6" fill="none" stroke="#4fd6fb" stroke-width="1.3"/></svg>
        hello@hearthsidevet.com.au
      </li>
      <li>
        <svg viewBox="0 0 20 20" fill="none" stroke="#2f86d8" stroke-width="1.3"><circle cx="10" cy="10" r="8"/><ellipse cx="10" cy="10" rx="3.5" ry="8"/><path d="M2 10h16M3.5 6h13M3.5 14h13"/></svg>
        www.hearthsidevet.com.au
      </li>
    </ul>

    <div class="pet-watermark" role="img" aria-label="Faint large silhouette of a dog and cat"></div>

    <footer class="address">
      <svg viewBox="0 0 20 20"><path d="M10 2L1 10h3v8h4.5v-5h3v5H16v-8h3z" fill="#2f86d8"/></svg>
      PO Box 5521 Kenmore Qld 4069
    </footer>
  </main>
</body>
</html>
```